Business Cards for a law firm

Business cards for our law firm. Use our silhoette logo and OAK PARTNERS - check our website (www.oakpartners.example)

Contact Information for Business Card

our silhouette logo, OAK PARTNERS, 800-555-0147, Dorian Pemberton, dorian@oakpartners.example

Requirements
Must have
• our silhouette logo, OAK PARTNERS, 800-555-0147, Dorian Pemberton, dorian@oakpartners.example

```html
<!DOCTYPE html>
<html lang="en">
<head>
<meta charset="utf-8">
<title>Oak Partners — Business Cards</title>
<link rel="stylesheet" href="https://fonts.googleapis.com/css2?family=Montserrat:wght@500;600&family=Open+Sans:wght@400;700&display=swap">
<style>
  :root{
    --backdrop:#1f1f21;
    --navy:#1c3370;
    --navy-deep:#172a5e;
    --silver:#c7cad2;
    --paper:#ffffff;
    --ink:#2b2b2b;
    --accent:#f2a31b;
  }
  *{margin:0;padding:0;box-sizing:border-box}
  html,body{width:1200px;height:977px;overflow:hidden;background:var(--backdrop)}
  .canvas{position:relative;width:1200px;height:977px}
  .card{position:absolute;left:280px;width:640px;height:370px;border-radius:22px;overflow:hidden}
  .card--front{top:92px;background:var(--navy)}
  .card--back{top:515px;background:var(--paper)}

  .brand{display:flex;align-items:center;gap:14px;font-family:"Montserrat",sans-serif;font-weight:600;letter-spacing:.14em;white-space:nowrap}
  .brand__mark{display:block;flex:none}
  .card--front .brand{position:absolute;left:0;right:0;top:0;bottom:0;justify-content:center;color:var(--silver);font-size:40px}
  .card--front .brand__mark{width:22px;height:22px;background:var(--silver)}
  .card--back .brand{position:absolute;right:42px;top:52px;color:var(--navy);font-size:24px;gap:10px}
  .card--back .brand__mark{width:14px;height:14px;background:var(--navy)}

  .person{position:absolute;left:46px;top:168px;font-family:"Open Sans",sans-serif}
  .person__name{color:var(--navy);font-weight:700;font-size:30px;letter-spacing:.01em;line-height:1}
  .person__role{color:var(--accent);font-size:19px;margin-top:6px}
  .divider{position:absolute;left:46px;right:40px;top:248px;height:1.5px;background:var(--navy)}
  .contact{position:absolute;left:46px;top:264px;list-style:none;font-family:"Open Sans",sans-serif;font-size:16px;color:var(--ink)}
  .contact__item{display:flex;align-items:center;gap:12px;height:28px}
  .contact__icon{width:14px;height:14px;fill:var(--navy);flex:none}
</style>
</head>
<body>
<main class="canvas">
  <section class="card card--front" aria-label="Card front">
    <div class="brand"><span class="brand__mark"></span>OAK PARTNERS</div>
  </section>

  <section class="card card--back" aria-label="Card back">
    <div class="brand"><span class="brand__mark"></span>OAK PARTNERS</div>
    <div class="person">
      <p class="person__name">DORIAN PEMBERTON</p>
      <p class="person__role">Attorney</p>
    </div>
    <div class="divider"></div>
    <ul class="contact">
      <li class="contact__item">
        <svg class="contact__icon" viewBox="0 0 24 24"><path d="M6.6 10.8a15.2 15.2 0 0 0 6.6 6.6l2.2-2.2c.3-.3.7-.4 1-.2 1.1.4 2.3.6 3.6.6.6 0 1 .4 1 1V20c0 .6-.4 1-1 1A17 17 0 0 1 3 4c0-.6.4-1 1-1h3.5c.6 0 1 .4 1 1 0 1.3.2 2.5.6 3.6.1.3 0 .7-.2 1z"/></svg>
        (800) 555-0147
      </li>
      <li class="contact__item">
        <svg class="contact__icon" viewBox="0 0 24 24"><path d="M2 5h20v14H2z" /><path d="M2 5l10 8 10-8" fill="none" stroke="#fff" stroke-width="2"/></svg>
        dorian@oakpartners.example
      </li>
      <li class="contact__item">
        <svg class="contact__icon" viewBox="0 0 24 24"><circle cx="12" cy="12" r="10"/><path d="M2 12h20M12 2c3 3 3 17 0 20M12 2c-3 3-3 17 0 20" fill="none" stroke="#fff" stroke-width="1.6"/></svg>
        www.oakpartners.example
      </li>
    </ul>
  </section>
</main>
</body>
</html>
```